Redesign of business card for Cedar Ridge Mechanical

We are looking for a new design for our business cards for Cedar Ridge Mechanical. We are a plumbing & HVAC construction company, operating on the West Coast of Canada and USA. Logo attached.
Industry/Entity Type
Construction - Plumbing & HVAC
Contact Information for Business Card
Name, address, phone numbers, email, website address
Look and feel
Each slider illustrates characteristics of the customer's brand and the style your logo design should communicate.

```html
<!DOCTYPE html>
<html lang="en">
<head>
<meta charset="utf-8">
<title>Cedar Ridge Mechanical – Business Cards</title>
<link rel="stylesheet" href="https://fonts.googleapis.com/css2?family=Open+Sans:wght@400;700&family=Oswald:wght@500&display=swap">
<style>
  :root {
    --stage: #6d6d6d;
    --card-white: #ffffff;
    --ink: #0a0a0a;
    --band-grey: #7a7a7a;
    --text-light: #ffffff;
    --shadow: rgba(0, 0, 0, 0.25);
  }
  * { margin: 0; padding: 0; box-sizing: border-box; }
  html, body {
    width: 1200px; height: 780px; overflow: hidden;
    background: var(--stage);
  }
  .canvas {
    position: relative; width: 1200px; height: 780px;
  }
  .card {
    position: absolute; top: 240px;
    width: 520px; height: 300px;
    background: var(--card-white);
    box-shadow: 0 6px 18px var(--shadow);
    overflow: hidden;
  }
  .card--front { left: 50px; }
  .card--back { left: 630px; }

  .front-band {
    position: absolute; inset: 0;
    width: 100%; height: 100%;
  }
  .contact {
    position: absolute; left: 28px; top: 32px;
    color: var(--text-light);
    font-family: "Open Sans", sans-serif;
  }
  .contact__name {
    font-weight: 700; font-size: 17px; letter-spacing: 0.5px;
    text-transform: uppercase; line-height: 1.1;
  }
  .contact__role {
    font-size: 12.5px; margin-bottom: 14px;
  }
  .contact__address {
    font-size: 12.5px; line-height: 1.35; margin-bottom: 14px;
  }
  .contact__list { list-style: none; font-size: 12.5px; line-height: 1.6; }
  .contact__list li { display: flex; align-items: center; gap: 6px; white-space: nowrap; }
  .contact__icon { width: 11px; height: 11px; flex: none; }

  .brand {
    position: absolute;
    display: flex; align-items: center; gap: 10px;
    font-family: "Oswald", sans-serif; font-weight: 500;
    color: var(--ink); text-transform: uppercase;
    line-height: 1.05;
  }
  .brand__mark {
    background: var(--ink); flex: none;
  }
  .card--front .brand { left: 292px; top: 112px; font-size: 24px; }
  .card--front .brand__mark { width: 22px; height: 22px; }
  .card--back .brand {
    left: 0; right: 0; top: 0; bottom: 0;
    justify-content: center; font-size: 32px;
  }
  .card--back .brand__mark { width: 30px; height: 30px; }
</style>
</head>
<body>
<main class="canvas">

  <section class="card card--front" aria-label="Business card, contact side">
    <svg class="front-band" viewBox="0 0 520 300" aria-hidden="true">
      <path d="M0 0 H312 C262 40 262 200 162 300 H0 Z" fill="var(--band-grey)"/>
      <path d="M0 0 H300 C250 40 250 200 150 300 H0 Z" fill="var(--ink)"/>
    </svg>

    <div class="contact">
      <p class="contact__name">Daniel Hayes</p>
      <p class="contact__role">Managing Director</p>
      <p class="contact__address">Your address, City<br>State, Zip 1234</p>
      <ul class="contact__list">
        <li>
          <svg class="contact__icon" viewBox="0 0 12 12" aria-hidden="true"><path d="M2.5 1 L4.5 1 L5.3 3.6 L4 4.6 C4.6 6 5.9 7.4 7.4 8 L8.4 6.7 L11 7.5 L11 9.5 C11 10.3 10.3 11 9.5 11 C5 11 1 7 1 2.5 C1 1.7 1.7 1 2.5 1 Z" fill="currentColor"/></svg>
          123 456 789
        </li>
        <li>
          <svg class="contact__icon" viewBox="0 0 12 12" aria-hidden="true"><rect x="1" y="2.5" width="10" height="7" fill="none" stroke="currentColor" stroke-width="1.2"/><path d="M1 2.5 L6 6.5 L11 2.5" fill="none" stroke="currentColor" stroke-width="1.2"/></svg>
          info@yourmail.com
        </li>
        <li>
          <svg class="contact__icon" viewBox="0 0 12 12" aria-hidden="true"><circle cx="6" cy="6" r="5" fill="none" stroke="currentColor" stroke-width="1.2"/><path d="M1 6 H11 M6 1 C3.5 4 3.5 8 6 11 M6 1 C8.5 4 8.5 8 6 11" fill="none" stroke="currentColor" stroke-width="1"/></svg>
          www.yourwebsite.com
        </li>
      </ul>
    </div>

    <div class="brand">
      <span class="brand__mark" aria-hidden="true"></span>
      <span class="brand__name">Cedar Ridge<br>Mechanical</span>
    </div>
  </section>

  <section class="card card--back" aria-label="Business card, brand side">
    <div class="brand">
      <span class="brand__mark" aria-hidden="true"></span>
      <span class="brand__name">Cedar Ridge Mechanical</span>
    </div>
  </section>

</main>
</body>
</html>
```